verdant terraces simple classy business card design

my name is colin barrow and I run a gardening business aimed at high class verdant terraces. the business name is verdant terraces and our logo was designed on pixel harbour .My clientel are anything from residential homes to businesses. I take pride in my work and know that I offer a service like no other in my area.
The business card will be used to represent my business and I want it to be not only rememberable, but simplistic and modern. Eye catching too. Of course I would like it relatable to gardening and appealing to the correct clientel - those being garden enthusiasts, prestigious homes and businesses that are after top of the line gardening services like no other on the market.
I am not a typical lawn mowing business so I don't want a typical card design that represents that. The gardens I work with are generally million dollar properties with owners who are very garden proud looking for upkeep and guidance from me along with sometimes whole new garden designs. I want the business cards to show to my clients that I take pride, as they do, in their garden. And I want them to know from my card that I am a professional, qualified horticulturist offering them a top of the line service for life. I want them to refer my business on. I want them to look at my business card and see class and professionalism in a modern unique bold way.
The card should be simple with the possibility of the logo on the front being embossed/debossed and my details on the back the card should have a organic garden feel it's very important to me that it is absolutely perfect
I am also very open to ideas and suggestions so look forward to seeing the designs. the business logo has been supplied with this project and I want the card to be double sided

Contact info is
Colin Barrow - Managing Director / Horticulturist
Phone : 0481 526 704
Email: colinbarrow@verdantterraces.example.au

Target Market(s)

high class gardens residential and commercial

Industry/Entity Type

Gardener

Contact Information for Business Card

Contact info is
Phone : 0481 526 704

PLEASE MAKE CARD DOUBLE SIDED

Requirements
Must have
• organic simple classy modern feel
• must flow with the current logo that has been supplied with this project
• Double sided
• Must explain in a simple way that I deal with high end gardens and I'm a qualified horticulturist
Nice to have
• embossed debossed logo
Should not have
• shouldn't be to busy or cheap looking

```html
<!DOCTYPE html>
<html lang="en">
<head>
<meta charset="utf-8">
<title>Verdant Terraces — Business Card</title>
<link href="https://fonts.googleapis.com/css2?family=Crimson+Text:wght@400;600&display=swap" rel="stylesheet">
<style>
  :root {
    --backdrop: #d9d9d7;
    --card: #efeef0;
    --leaf: #55a84a;
    --leaf-soft: #8cc67f;
    --ink: #2e2e2e;
    --ink-muted: #555555;
  }
  * { box-sizing: border-box; margin: 0; padding: 0; }
  html, body {
    width: 1200px;
    height: 799px;
    overflow: hidden;
    background: var(--backdrop);
    font-family: "Crimson Text", Georgia, serif;
  }
  .stage {
    position: relative;
    width: 1200px;
    height: 799px;
    display: flex;
    justify-content: center;
    align-items: center;
    gap: 60px;
  }
  .card {
    position: relative;
    width: 330px;
    height: 540px;
    background: var(--card);
    box-shadow: 0 6px 18px rgba(0, 0, 0, 0.18);
    overflow: hidden;
  }

  /* Front */
  .card-front {
    display: flex;
    justify-content: center;
    align-items: center;
    padding: 0 40px 40px;
  }
  .brand {
    display: flex;
    align-items: center;
    gap: 16px;
  }
  .brand-dot {
    flex: none;
    width: 14px;
    height: 14px;
    border-radius: 50%;
    background: var(--leaf);
  }
  .brand-name {
    display: flex;
    flex-direction: column;
    color: var(--leaf);
    font-weight: 400;
    font-size: 24px;
    line-height: 1.15;
    letter-spacing: 0.14em;
    text-transform: uppercase;
  }

  /* Back */
  .foliage {
    position: absolute;
    top: 0;
    right: 0;
    width: 250px;
    height: 345px;
  }
  .details {
    position: absolute;
    left: 34px;
    right: 24px;
    bottom: 52px;
  }
  .holder-name {
    color: var(--leaf);
    font-size: 21px;
    font-weight: 400;
    letter-spacing: 0.06em;
    text-transform: uppercase;
    line-height: 1.1;
  }
  .holder-role {
    color: var(--ink);
    font-size: 13px;
    margin-bottom: 14px;
  }
  .contact {
    list-style: none;
    color: var(--ink-muted);
    font-size: 13px;
    line-height: 1.45;
  }
</style>
</head>
<body>
<main class="stage">
  <section class="card card-front" aria-label="Card front">
    <div class="brand">
      <span class="brand-dot"></span>
      <span class="brand-name"><span>Verdant</span><span>Terraces</span></span>
    </div>
  </section>

  <section class="card card-back" aria-label="Card back">
    <svg class="foliage" viewBox="0 0 250 345" role="img" aria-label="Green leafy tree illustration with a trunk running down the right edge">
      <defs>
        <radialGradient id="foliage-fill" cx="0.5" cy="0.35" r="0.65">
          <stop offset="0" stop-color="#55a84a" stop-opacity="0.85"/>
          <stop offset="0.7" stop-color="#8cc67f" stop-opacity="0.45"/>
          <stop offset="1" stop-color="#efeef0" stop-opacity="0"/>
        </radialGradient>
      </defs>
      <rect width="250" height="345" fill="url(#foliage-fill)"/>
      <rect x="232" y="170" width="18" height="175" fill="#55a84a"/>
    </svg>

    <div class="details">
      <h1 class="holder-name">Colin Barrow</h1>
      <p class="holder-role">Managing Director / Horticulturist</p>
      <ul class="contact">
        <li>0481 526 704</li>
        <li>colinbarrow@verdantterraces.example.au</li>
        <li>verdantterraces.example.au</li>
      </ul>
    </div>
  </section>
</main>
</body>
</html>
```